Veranix - Solution provider in business consulting

Veranix is a swiss based company providing solutions for developing markets. The business covers various fields of business consulting, such as supply chain, product costs, quality management and manufacturing management. The Business operates in a efficient, straight and solution oriented manner.
The final design should communicate these characteristics. Asian people as well as as western people shall identify the qualities of the company at first sight.
The customer needs business cards with a simple view but an recognizable design, printed in high quality. Engraved elements such as the globe or simple words are possible.
Available colors are: (RAL)
102/102/102
51/102/102
153/204/153
255/102/51
Font: Calibri

```html
<!DOCTYPE html>
<html lang="en">
<head>
<meta charset="utf-8">
<title>Veranix business card</title>
<link rel="stylesheet" href="https://fonts.googleapis.com/css2?family=Carlito:wght@400;700&display=swap">
<style>
  :root {
    --backdrop: #ececec;
    --card: #b3b3b3;
    --ink-dark: #666666;
    --ink-name: #6b6b6b;
    --ink-text: #1f1f1f;
    --icon: #555555;
  }
  * { margin: 0; padding: 0; box-sizing: border-box; }
  html, body { width: 1200px; height: 900px; overflow: hidden; }
  body {
    position: relative;
    background: var(--backdrop);
    font-family: "Carlito", Calibri, sans-serif;
  }
  .card {
    position: absolute;
    width: 554px;
    height: 342px;
    background: var(--card);
    overflow: hidden;
  }
  .card--front { left: 240px; top: 62px; }
  .card--back { left: 458px; top: 519px; }

  .holder { position: absolute; left: 38px; top: 36px; }
  .holder__name { font-size: 21px; font-weight: 700; color: var(--ink-name); line-height: 1.1; }
  .holder__role { font-size: 15px; color: var(--ink-text); line-height: 1.3; }

  .contact { position: absolute; left: 38px; top: 172px; list-style: none; }
  .contact__item {
    display: flex; align-items: center; gap: 9px;
    font-size: 15.5px; color: var(--ink-text); height: 23px;
  }
  .contact__icon { width: 13px; height: 13px; fill: var(--icon); flex: none; }

  .address {
    position: absolute; left: 38px; top: 276px;
    font-size: 15.5px; line-height: 23px; color: var(--ink-text); font-style: normal;
  }

  .globe-decoration {
    position: absolute; left: 213px; top: -12px;
    width: 356px; height: 356px; border-radius: 50%;
    background: radial-gradient(circle at 60% 40%, #7a7a7a, var(--ink-dark));
  }

  .wordmark {
    position: absolute; left: 0; right: 0; top: 128px;
    text-align: center; font-size: 64px; font-weight: 400;
    color: var(--ink-dark); letter-spacing: 2px; line-height: 1;
  }
</style>
</head>
<body>
  <section class="card card--front" aria-label="Business card front">
    <div class="globe-decoration" role="img" aria-label="Engraved globe showing Asia"></div>
    <header class="holder">
      <p class="holder__name">Lena Marti</p>
      <p class="holder__role">CEO</p>
    </header>
    <ul class="contact">
      <li class="contact__item">
        <svg class="contact__icon" viewBox="0 0 13 13" aria-hidden="true"><path d="M3.5 0h6a1 1 0 0 1 1 1v11a1 1 0 0 1-1 1h-6a1 1 0 0 1-1-1V1a1 1 0 0 1 1-1zm.5 1.5v8.5h5V1.5zm2.5 9.3a.7.7 0 1 0 0 1.4.7.7 0 0 0 0-1.4z"/></svg>
        +41 79 000 4821
      </li>
      <li class="contact__item">
        <svg class="contact__icon" viewBox="0 0 13 13" aria-hidden="true"><path d="M2.6.5l2 2.4-1.2 1.6a8 8 0 0 0 5.1 5.1l1.6-1.2 2.4 2-1.2 2.1C6 12.5.5 7 .5 1.7z"/></svg>
        +41 71 000 3367
      </li>
      <li class="contact__item">
        <svg class="contact__icon" viewBox="0 0 13 13" aria-hidden="true"><path d="M1 2.5h11v8H1zm.8.8v.4l4.7 3 4.7-3v-.4z"/></svg>
        lena.marti@veranix.ch
      </li>
      <li class="contact__item">
        <svg class="contact__icon" viewBox="0 0 13 13" aria-hidden="true"><circle cx="6.5" cy="6.5" r="6"/><path d="M6.5 1.5v10M1.5 6.5h10" stroke="#b3b3b3" stroke-width="1" fill="none"/></svg>
        www.veranix.ch
      </li>
    </ul>
    <address class="address">
      Veranix GmbH Lindenweg 14<br>
      8400 Talwil Switzerland
    </address>
  </section>

  <section class="card card--back" aria-label="Business card back">
    <p class="wordmark">veranix</p>
  </section>
</body>
</html>
```